Business card for a new cabinet shop company named Veloran Cabinets for high end cabinets

Design a business card, thinking dark rich green with colours to speak of high end luxury ie; cream, gold, black possibly

Mitchell Tarrowby
Director Craftsman
Email: info@veloranjoinery-example.com.au
Instagram : @veloran.cabinets

```html
<!DOCTYPE html>
<html lang="en">
<head>
<meta charset="utf-8">
<title>Veloran Cabinets – Business Card</title>
<link rel="stylesheet" href="https://fonts.googleapis.com/css2?family=Montserrat:wght@300;400;500;700&display=swap">
<style>
  :root {
    --backdrop: #2b2b2b;
    --card-green: #005f00;
    --gold: #c9a764;
    --cream: #ffffff;
    --rule: rgba(255, 255, 255, 0.85);
  }
  * { box-sizing: border-box; margin: 0; padding: 0; }
  html, body {
    width: 1200px;
    height: 694px;
    overflow: hidden;
    background: var(--backdrop);
    font-family: "Montserrat", sans-serif;
  }
  .stage {
    width: 1200px;
    height: 694px;
    display: flex;
    align-items: center;
    justify-content: center;
    gap: 40px;
  }
  .card {
    width: 540px;
    height: 310px;
    background: var(--card-green);
    border-radius: 22px;
    position: relative;
  }
  .card--front {
    display: flex;
    align-items: center;
    justify-content: center;
  }
  .brand-name {
    color: var(--gold);
    font-weight: 500;
    font-size: 40px;
    letter-spacing: 0.02em;
    white-space: nowrap;
  }
  .card--back .brand-name {
    position: absolute;
    top: 48px;
    right: 44px;
    font-size: 28px;
  }
  .holder {
    position: absolute;
    left: 40px;
    top: 150px;
  }
  .holder-name {
    color: var(--gold);
    font-weight: 700;
    font-size: 28px;
    line-height: 1.1;
  }
  .holder-title {
    color: var(--cream);
    font-weight: 400;
    font-size: 16px;
    margin-top: 6px;
  }
  .divider {
    position: absolute;
    left: 40px;
    right: 40px;
    top: 232px;
    height: 1px;
    background: var(--rule);
  }
  .contacts {
    position: absolute;
    left: 40px;
    right: 40px;
    top: 250px;
    display: flex;
    justify-content: space-between;
    align-items: center;
  }
  .contact {
    display: flex;
    align-items: center;
    gap: 8px;
    color: var(--cream);
    font-weight: 400;
    font-size: 13px;
  }
  .contact-icon { flex: none; }
</style>
</head>
<body>
  <main class="stage">
    <section class="card card--front">
      <div class="brand-name">Veloran Cabinets</div>
    </section>

    <section class="card card--back">
      <div class="brand-name">Veloran Cabinets</div>

      <div class="holder">
        <div class="holder-name">Mitchell Tarrowby</div>
        <div class="holder-title">Director Craftsman</div>
      </div>

      <div class="divider"></div>

      <div class="contacts">
        <div class="contact contact--email">
          <svg class="contact-icon" width="16" height="12" viewBox="0 0 16 12" aria-hidden="true">
            <rect x="0" y="0" width="16" height="12" fill="var(--gold)"/>
            <polyline points="0,0 8,7 16,0" fill="none" stroke="var(--card-green)" stroke-width="1.6"/>
          </svg>
          <span>info@veloranjoinery-example.com.au</span>
        </div>
        <div class="contact contact--social">
          <svg class="contact-icon" width="12" height="12" viewBox="0 0 12 12" aria-hidden="true">
            <circle cx="6" cy="6" r="5" fill="none" stroke="var(--gold)" stroke-width="1.5"/>
          </svg>
          <span>@veloran.cabinets</span>
        </div>
      </div>
    </section>
  </main>
</body>
</html>
```